Private Investigation Business Card Design

I need a business card for a new private investigation company named Brisk Inquiries. I perform mainly surveillance jobs, vehicle repossessions, document serves etc. The final design should aim for a professional look. The logo has a magnifying glass with stick man arms and legs and is in a running action to show the "Brisk" aspect of the name. If the colour scheme could remain the same as the website www.briskinquiries-demo.com.au with silvers,blacks and a couple electric blue highlights.
Industry/Entity Type
Business
Contact Information for Business Card
Morgan Kellaway
Brisk Inquiries
0487316204
PO Box 58, Carnwell NSW 2291
info@briskinquiries-demo.com.au
www.briskinquiries-demo.com.au
Look and feel

```html
<!DOCTYPE html>
<html lang="en">
<head>
<meta charset="utf-8">
<title>Brisk Inquiries – Business Cards</title>
<link rel="stylesheet" href="https://fonts.googleapis.com/css2?family=Open+Sans:wght@400;600;700&display=swap">
<style>
  :root {
    --backdrop: #8f8f8f;
    --card: #ffffff;
    --electric-blue: #4a9bd6;
    --ink: #1c1c1c;
    --silver: #8a8a8a;
    --text-grey: #6f6f6f;
    --icon: #2a2a2a;
  }
  * { margin: 0; padding: 0; box-sizing: border-box; }
  html, body {
    width: 1200px; height: 900px; overflow: hidden;
    background: radial-gradient(ellipse at 50% 45%, #d6d6d6 0%, #a9a9a9 55%, var(--backdrop) 100%);
    font-family: "Open Sans", sans-serif;
  }
  .sheet {
    position: relative; width: 1200px; height: 900px;
    display: flex; flex-direction: column; align-items: center; justify-content: center; gap: 44px;
  }
  .card {
    position: relative; width: 680px; height: 388px;
    background: var(--card);
    box-shadow: 0 14px 30px rgba(0,0,0,0.35);
    overflow: hidden;
  }
  .card__band {
    position: absolute; left: 0; right: 0; bottom: 0; height: 52px;
    background: var(--electric-blue);
  }
  .card__tab {
    position: absolute; left: 0; top: 150px; width: 24px; height: 110px;
    background: var(--electric-blue);
  }
  .holder-name {
    font-size: 25px; letter-spacing: 0.3px; line-height: 1; text-transform: uppercase;
  }
  .holder-name__first { color: var(--silver); font-weight: 400; }
  .holder-name__last { color: var(--ink); font-weight: 700; }
  .holder-company { color: var(--electric-blue); font-size: 15px; margin-top: 6px; }

  /* front: contact card */
  .card--contact .identity { position: absolute; left: 106px; top: 56px; }
  .contact-list {
    position: absolute; left: 74px; top: 148px; list-style: none;
    display: flex; flex-direction: column; gap: 11px;
  }
  .contact-list__item {
    display: flex; align-items: center; gap: 18px;
    font-size: 15px; color: var(--text-grey);
  }
  .contact-list__icon { width: 24px; height: 18px; flex: none; }

  .brand {
    position: absolute; right: 44px; bottom: 84px;
    display: flex; align-items: center; gap: 10px;
  }
  .brand__dot { width: 14px; height: 14px; border-radius: 50%; background: var(--silver); }
  .brand__name { font-size: 30px; font-weight: 700; color: var(--silver); letter-spacing: 0.5px; }

  /* back: name card */
  .card--name .name-row {
    position: absolute; left: 250px; top: 92px;
    display: flex; align-items: center; gap: 24px;
  }
  .card--name .identity { text-align: left; }
  .card--name .holder-name { font-size: 24px; }
  .card--name .holder-company { font-size: 14px; margin-top: 2px; }
  .divider { width: 2px; height: 34px; background: var(--electric-blue); }
  .website { font-size: 15px; color: var(--text-grey); letter-spacing: 0.3px; }
  .card--name .brand { bottom: 90px; right: 40px; }
  .card--name .brand__name { font-size: 40px; }
  .card--name .brand__dot { width: 18px; height: 18px; }
</style>
</head>
<body>
<main class="sheet">

  <section class="card card--contact" aria-label="Business card front">
    <div class="card__tab"></div>
    <div class="identity">
      <h1 class="holder-name"><span class="holder-name__first">Morgan</span> <span class="holder-name__last">Kellaway</span></h1>
      <p class="holder-company">Brisk Inquiries</p>
    </div>
    <ul class="contact-list">
      <li class="contact-list__item">
        <svg class="contact-list__icon" viewBox="0 0 24 18" aria-hidden="true"><rect x="6" y="1" width="11" height="16" rx="2" fill="none" stroke="var(--icon)" stroke-width="1.8"/><rect x="8.5" y="3.5" width="6" height="5" fill="var(--icon)"/><circle cx="11.5" cy="13" r="1.3" fill="var(--icon)"/></svg>
        <span>0487316204</span>
      </li>
      <li class="contact-list__item">
        <svg class="contact-list__icon" viewBox="0 0 24 18" aria-hidden="true"><circle cx="12" cy="9" r="7.5" fill="none" stroke="var(--icon)" stroke-width="1.6"/><ellipse cx="12" cy="9" rx="3.2" ry="7.5" fill="none" stroke="var(--icon)" stroke-width="1.2"/><line x1="4.5" y1="9" x2="19.5" y2="9" stroke="var(--icon)" stroke-width="1.2"/></svg>
        <span>www.briskinquiries-demo.com.au</span>
      </li>
      <li class="contact-list__item">
        <svg class="contact-list__icon" viewBox="0 0 24 18" aria-hidden="true"><rect x="2" y="3" width="20" height="13" fill="var(--icon)"/><polyline points="2,3 12,11 22,3" fill="none" stroke="#fff" stroke-width="1.4"/></svg>
        <span>info@briskinquiries-demo.com.au</span>
      </li>
      <li class="contact-list__item">
        <svg class="contact-list__icon" viewBox="0 0 24 18" aria-hidden="true"><line x1="11" y1="1" x2="11" y2="17" stroke="var(--icon)" stroke-width="2"/><path d="M3 4h15l3 2.5-3 2.5H3z" fill="var(--icon)"/><path d="M20 10H6l-3 2.5L6 15h14z" fill="var(--icon)"/></svg>
        <span>PO Box 58, Carnwell NSW 2291</span>
      </li>
    </ul>
    <div class="brand">
      <span class="brand__name">Brisk Inquiries</span>
      <span class="brand__dot"></span>
    </div>
    <div class="card__band"></div>
  </section>

  <section class="card card--name" aria-label="Business card back">
    <div class="name-row">
      <div class="identity">
        <h2 class="holder-name"><span class="holder-name__first">Morgan</span> <span class="holder-name__last">Kellaway</span></h2>
        <p class="holder-company">Brisk Inquiries</p>
      </div>
      <span class="divider"></span>
      <span class="website">www.briskinquiries-demo.com.au</span>
    </div>
    <div class="brand">
      <span class="brand__name">Brisk Inquiries</span>
      <span class="brand__dot"></span>
    </div>
    <div class="card__band"></div>
  </section>

</main>
</body>
</html>
```